Zenqo - revolutionary mobile payment

The app is a P2P money trasfert, without the using of credit card or bank circuits it can transfer electronic money from one person to another consumers simply and immediatelly.
You can use the color you want, but the message we need to transert to consumer is simplicity, safety and coolness.
In attach the logo of the company and the wireframe of thre page of the app.
The goal is to design the page of the app with a clear, simple and intuitive graphic.
Updates

I have upgrade the brief with important information and detail, many thanks

Target Market(s)

all the people

Industry/Entity Type

Credit Card

Requirements
Must have
• You have to design one icon for each button in the first page, (shop is: where to shop)
in the second one a new intuitive image (instead of the hand) that let the user to understand that with a simple swipe he can process the payment
Nice to have
• You can include or esxclude what you want or belive can improve user experience of the app
Should not have
• too much color, too much button or information

```html
<!DOCTYPE html>
<html lang="en">
<head>
<meta charset="utf-8">
<title>Zenqo – Home</title>
<link href="https://fonts.googleapis.com/css2?family=Montserrat:wght@400;500;600;700&display=swap" rel="stylesheet">
<style>
  :root {
    --canvas: #c3c6cb;
    --status-bg: #f2f2f2;
    --nav-bg: #e9e9ea;
    --ink: #1c1c1e;
    --brand: #24407a;
    --band-a: #2a3566;
    --band-b: #4a2f63;
    --band-c: #55678f;
    --tile: #2e4272;
    --tile-edge: #3a5186;
    --white: #ffffff;
    --blur-red: #c8283c;
    --blur-grey: #a9b0b4;
    --blur-blue: #3a4a78;
  }
  * { box-sizing: border-box; margin: 0; padding: 0; }
  html, body { width: 1200px; height: 1195px; overflow: hidden; }
  body {
    background: var(--canvas);
    font-family: "Montserrat", sans-serif;
    color: var(--ink);
    position: relative;
  }
  .screen {
    position: absolute;
    left: 320px; top: 100px;
    width: 560px; height: 995px;
    overflow: hidden;
    background: var(--blur-grey);
    box-shadow: 0 20px 50px rgba(0,0,0,0.18);
  }
  .status-bar {
    height: 36px;
    background: var(--status-bg);
    display: flex; align-items: center; justify-content: space-between;
    padding: 0 14px;
    font-size: 15px; font-weight: 500;
  }
  .status-left, .status-right { display: flex; align-items: center; gap: 6px; width: 150px; }
  .status-right { justify-content: flex-end; }
  .status-time { font-weight: 600; }
  .nav-bar {
    height: 60px;
    background: linear-gradient(var(--nav-bg), #dcdddf);
    display: flex; align-items: center; justify-content: space-between;
    padding: 0 18px;
    border-bottom: 1px solid #c9cacc;
  }
  .brand { display: flex; align-items: center; gap: 8px; color: var(--brand); font-weight: 700; font-size: 24px; }
  .brand-dot { width: 22px; height: 22px; border-radius: 50%; background: var(--brand); }
  .profile-band {
    height: 170px;
    position: relative;
    background: linear-gradient(115deg, var(--band-a) 0%, var(--band-b) 45%, var(--band-c) 100%);
    display: flex; align-items: center;
    padding: 0 26px;
    gap: 24px;
    color: var(--white);
  }
  .avatar {
    width: 108px; height: 108px; border-radius: 50%;
    border: 4px solid var(--white);
    background: radial-gradient(circle at 50% 40%, #c9a894, #4f5b3c 75%);
    flex: none;
  }
  .profile-name { font-size: 30px; font-weight: 600; letter-spacing: 0.3px; }
  .profile-phone { font-size: 15px; font-weight: 400; margin-top: 4px; opacity: 0.9; letter-spacing: 1px; }
  .edit-button {
    position: absolute; right: 22px; top: 18px;
    width: 34px; height: 34px; border-radius: 50%;
    background: var(--white);
    display: flex; align-items: center; justify-content: center;
  }
  .actions {
    height: 729px;
    position: relative;
    background:
      radial-gradient(ellipse 140px 420px at 48% 50%, rgba(214,58,84,0.95), transparent 70%),
      radial-gradient(ellipse 420px 120px at 50% 46%, rgba(200,40,60,0.8), transparent 70%),
      radial-gradient(ellipse 300px 260px at 20% 90%, rgba(160,20,40,0.9), transparent 70%),
      radial-gradient(ellipse 260px 300px at 90% 15%, rgba(190,200,200,0.9), transparent 70%),
      linear-gradient(160deg, var(--blur-grey), var(--blur-blue) 60%, var(--blur-red));
    display: grid;
    grid-template-columns: 232px 232px;
    grid-template-rows: 232px 232px;
    gap: 28px;
    justify-content: center; align-content: center;
  }
  .action-tile {
    background: var(--tile);
    border-top: 1px solid var(--tile-edge);
    border-radius: 4px;
    display: flex; flex-direction: column; align-items: center; justify-content: center;
    gap: 14px;
    color: var(--white);
    box-shadow: 0 6px 16px rgba(0,0,0,0.25);
  }
  .action-label { font-size: 22px; font-weight: 600; }
  .action-icon { width: 120px; height: 96px; }
</style>
</head>
<body>
  <main class="screen">
    <div class="status-bar">
      <div class="status-left">
        <span>●●●○○</span><span>NOVA</span>
        <svg width="18" height="14" viewBox="0 0 18 14"><path d="M1 5a12 12 0 0 1 16 0M4 8a8 8 0 0 1 10 0M7 11a3.5 3.5 0 0 1 4 0" fill="none" stroke="#1c1c1e" stroke-width="2" stroke-linecap="round"/></svg>
      </div>
      <span class="status-time">4:21 PM</span>
      <div class="status-right">
        <span>22%</span>
        <svg width="30" height="14" viewBox="0 0 30 14"><rect x="1" y="1" width="25" height="12" rx="2" fill="none" stroke="#1c1c1e" stroke-width="1.5"/><rect x="3" y="3" width="6" height="8" fill="#1c1c1e"/><rect x="27" y="4.5" width="2" height="5" fill="#1c1c1e"/></svg>
      </div>
    </div>

    <header class="nav-bar">
      <svg class="settings-icon" width="30" height="30" viewBox="0 0 24 24" aria-label="Settings"><path fill="#333" d="M19.4 13a7.5 7.5 0 0 0 0-2l2.1-1.6-2-3.5-2.5 1a7 7 0 0 0-1.7-1L15 3h-4l-.4 2.9a7 7 0 0 0-1.7 1l-2.5-1-2 3.5L6.5 11a7.5 7.5 0 0 0 0 2l-2.1 1.6 2 3.5 2.5-1a7 7 0 0 0 1.7 1L11 21h4l.4-2.9a7 7 0 0 0 1.7-1l2.5 1 2-3.5zM13 15.5a3.5 3.5 0 1 1 0-7 3.5 3.5 0 0 1 0 7z"/></svg>
      <div class="brand"><span class="brand-dot"></span><span>Zenqo</span></div>
    </header>

    <section class="profile-band">
      <div class="avatar" role="img" aria-label="User profile photo"></div>
      <div class="profile-info">
        <div class="profile-name">Marcus Bellamy</div>
        <div class="profile-phone">+39 312 000 4417</div>
      </div>
      <div class="edit-button">
        <svg width="16" height="16" viewBox="0 0 16 16"><path d="M3 11l7-7 2 2-7 7H3z" fill="#1c1c1e"/><rect x="10.5" y="1.5" width="3" height="3" transform="rotate(45 12 3)" fill="#1c1c1e"/></svg>
      </div>
    </section>

    <section class="actions">
      <div class="action-tile pay">
        <svg class="action-icon" viewBox="0 0 120 96">
          <rect x="30" y="26" width="74" height="46" rx="5" fill="#fff"/>
          <rect x="30" y="36" width="74" height="8" fill="#2e4272"/>
          <circle cx="90" cy="60" r="8" fill="#2e4272"/>
          <text x="90" y="64" font-size="11" font-weight="700" fill="#fff" text-anchor="middle" font-family="Montserrat, sans-serif">€</text>
          <path d="M8 84h40" stroke="#fff" stroke-width="5" stroke-linecap="round"/>
          <path d="M40 76l10 8-10 8" fill="none" stroke="#fff" stroke-width="5" stroke-linecap="round" stroke-linejoin="round"/>
        </svg>
        <span class="action-label">Pay</span>
      </div>
      <div class="action-tile ask">
        <svg class="action-icon" viewBox="0 0 120 96">
          <rect x="18" y="34" width="84" height="52" rx="4" fill="#fff"/>
          <path d="M18 38l42 26 42-26" fill="none" stroke="#2e4272" stroke-width="4"/>
          <path d="M46 6v20h-10l14 14 14-14h-10V6z" fill="#fff"/>
          <circle cx="88" cy="30" r="13" fill="#fff" stroke="#2e4272" stroke-width="3"/>
          <text x="88" y="36" font-size="16" font-weight="700" fill="#2e4272" text-anchor="middle" font-family="Montserrat, sans-serif">€</text>
        </svg>
        <span class="action-label">Ask</span>
      </div>
      <div class="action-tile account">
        <svg class="action-icon" viewBox="0 0 120 96">
          <circle cx="60" cy="22" r="18" fill="#fff"/>
          <path d="M24 92V64q0-18 18-20h36q18 2 18 20v28z" fill="#fff"/>
          <path d="M52 44l8 10 8-10" fill="none" stroke="#2e4272" stroke-width="3"/>
          <path d="M60 54l-4 24 4 6 4-6z" fill="#2e4272"/>
          <rect x="72" y="66" width="14" height="3" fill="#2e4272"/>
        </svg>
        <span class="action-label">Account</span>
      </div>
      <div class="action-tile shop">
        <svg class="action-icon" viewBox="0 0 120 96">
          <path d="M10 28l30-10 40 10 30-10v60l-30 10-40-10-30 10z" fill="#fff"/>
          <path d="M40 18v60M80 28v60" stroke="#2e4272" stroke-width="2"/>
          <path d="M60 8a16 16 0 0 0-16 16c0 12 16 30 16 30s16-18 16-30A16 16 0 0 0 60 8z" fill="#2e4272" stroke="#fff" stroke-width="3"/>
          <circle cx="60" cy="24" r="6" fill="#fff"/>
        </svg>
        <span class="action-label">Shop</span>
      </div>
    </section>
  </main>
</body>
</html>
```